Brisk Coatings business card for residential and commercial painting

A clean, professional design. Easy to read
Eye catching and elegant
Front could have some color variations
On the back of card I would like all black with signature logo

*Attached is my current business card and the items I want displayed

Contact Information for Business Card

Email, phone number, website, and owner name

Font styles to use
Serif

Requirements
Must have
• My logo with cool design and perhaps some paint splatter

```html
<!DOCTYPE html>
<html lang="en">
<head>
<meta charset="utf-8">
<title>Brisk Coatings – Business Card</title>
<link href="https://fonts.googleapis.com/css2?family=Roboto:wght@400;500&display=swap" rel="stylesheet">
<style>
  :root {
    --backdrop: #6b6767;
    --card-dark: #36373a;
    --card-dark-deep: #2f3033;
    --logo-ink: #1d1e20;
    --paper: #f1f1f0;
    --rule: #b9b9b9;
    --brand-blue: #0f6fba;
    --name-blue: #1672c4;
    --text-light: #f2f2f2;
  }
  * { box-sizing: border-box; margin: 0; padding: 0; }
  html, body { width: 1200px; height: 1200px; overflow: hidden; }
  body {
    background: var(--backdrop);
    font-family: "Roboto", Arial, sans-serif;
    position: relative;
  }
  .card {
    position: absolute;
    left: 298px;
    width: 594px;
    height: 350px;
    border-radius: 22px;
    overflow: hidden;
  }

  /* Back of card */
  .card-back { top: 198px; background: var(--paper); }
  .card-back .brand-panel {
    position: absolute; left: 0; top: 0; width: 100%; height: 210px;
    background: var(--card-dark);
    display: flex; align-items: center; justify-content: center;
  }
  .card-back .wordmark {
    font-weight: 500; font-size: 46px; letter-spacing: 1px;
    color: var(--logo-ink); text-transform: uppercase;
  }
  .card-back .note-line {
    position: absolute; left: 35px; right: 34px; height: 2px;
    background: var(--rule);
  }

  /* Front of card */
  .card-front { top: 636px; background: var(--card-dark-deep); }
  .card-front .art { position: absolute; inset: 0; }
  .card-front .brand-block {
    position: absolute; left: 54px; top: 130px;
    display: flex; align-items: flex-start; gap: 12px;
  }
  .card-front .brand-dot {
    width: 14px; height: 14px; background: #fff; margin-top: 12px;
  }
  .card-front .wordmark {
    font-weight: 500; font-size: 36px; line-height: 40px;
    color: #fff; text-transform: uppercase;
  }
  .owner {
    position: absolute; right: 34px; top: 72px; text-align: right;
  }
  .owner-name { font-weight: 500; font-size: 23px; color: var(--name-blue); line-height: 28px; }
  .owner-role { font-size: 16px; color: var(--text-light); line-height: 24px; }
  .contact-list {
    position: absolute; right: 34px; top: 186px; list-style: none;
  }
  .contact-list li {
    display: flex; align-items: center; justify-content: flex-end; gap: 12px;
    font-size: 16px; color: var(--text-light); height: 21px;
  }
  .contact-list svg { width: 14px; height: 14px; fill: var(--brand-blue); }
  .tagline {
    position: absolute; left: 254px; right: 0; top: 301px; height: 26px;
    text-align: center; font-size: 15px; line-height: 26px; color: var(--text-light);
    padding-right: 10px;
  }
</style>
</head>
<body>

<section class="card card-back" aria-label="Card back">
  <div class="brand-panel">
    <span class="wordmark">Brisk Coatings</span>
  </div>
  <div class="note-line" style="top:247px"></div>
  <div class="note-line" style="top:282px"></div>
  <div class="note-line" style="top:317px"></div>
</section>

<section class="card card-front" aria-label="Card front">
  <svg class="art" viewBox="0 0 594 350" width="594" height="350" aria-hidden="true">
    <path d="M0 0 H247 Q306 150 298 190 Q290 282 235 350 H0 Z" fill="#ffffff"/>
    <path d="M0 0 H240 Q298 150 290 190 Q283 280 227 350 H0 Z" fill="var(--brand-blue)"/>
    <path d="M256 299 L420 297 L594 296 V328 L430 331 L300 330 L254 331 Z" fill="var(--brand-blue)"/>
  </svg>

  <div class="brand-block">
    <span class="brand-dot"></span>
    <span class="wordmark">Brisk<br>Coatings</span>
  </div>

  <div class="owner">
    <div class="owner-name">Marcus "MO"</div>
    <div class="owner-role">Owner - Licensed &amp; Insured</div>
  </div>

  <ul class="contact-list">
    <li>931-555-0147
      <svg viewBox="0 0 16 16"><path d="M3 2h3l1.5 3.5-2 1.2a8 8 0 0 0 3.8 3.8l1.2-2L14 10v3a1 1 0 0 1-1 1A11 11 0 0 1 2 3a1 1 0 0 1 1-1z"/></svg>
    </li>
    <li>hello@briskcoatingstn.com
      <svg viewBox="0 0 16 16"><path d="M1 3h14v10H1z M2 4l6 5 6-5" stroke="#343538" stroke-width="1"/></svg>
    </li>
    <li>www.briskcoatingstn.com
      <svg viewBox="0 0 16 16"><circle cx="8" cy="8" r="7"/><path d="M1 8h14M8 1v14M3 4h10M3 12h10" stroke="#343538" stroke-width="0.8" fill="none"/></svg>
    </li>
  </ul>

  <div class="tagline">Painting Your Vision</div>
</section>

</body>
</html>
```